We need a business card design for a new company located in Missouri City, TX, entitled 'BrightPath Chiropractic & Holistic Center'. Our services include restoration of health and vitality, spinal exam, health assessment, dietary & fitness programs, lymphatic & therapeutic massage, detox & remineralize body wraps, far infrared sauna therapy

Industry/Entity Type

Business

Contact Information for Business Card

BrightPath Chiropractic & Holistic Center, Marlene Okafor LMT, 4215 Elm Ridge Rd., Suite 310, Missouri City, TX 77482, 281-555-0193

```html
<!DOCTYPE html>
<html lang="en">
<head>
<meta charset="utf-8">
<title>BrightPath Chiropractic &amp; Holistic Center – Business Card</title>
<link rel="stylesheet" href="https://fonts.googleapis.com/css2?family=Open+Sans:wght@400;600&family=Noto+Serif:wght@700&display=swap">
<style>
  :root {
    --page: #efece8;
    --card-top: #d8d4ce;
    --card-bottom: #cbbeb6;
    --brand-blue: #1b5b87;
    --brand-teal: #17a58c;
    --brand-grey: #6d6b6a;
    --ink: #1e1e1e;
    --white: #ffffff;
  }
  * { margin: 0; padding: 0; box-sizing: border-box; }
  html, body { width: 1189px; height: 1200px; overflow: hidden; }
  body {
    background: var(--page);
    font-family: "Open Sans", sans-serif;
    color: var(--ink);
    position: relative;
  }
  .card {
    position: absolute;
    left: 136px;
    width: 916px;
    height: 522px;
    background: linear-gradient(to bottom, var(--card-top), var(--card-bottom));
    box-shadow: 0 4px 14px rgba(0,0,0,0.18);
    overflow: hidden;
  }
  .card--front { top: 46px; }
  .card--back { top: 630px; }

  .accent-disc {
    position: absolute;
    right: -150px;
    top: 40px;
    width: 440px;
    height: 440px;
    border-radius: 50%;
    background: radial-gradient(circle, rgba(120,160,160,0.22), rgba(120,160,160,0.05) 70%, transparent);
  }

  /* Front */
  .wordmark {
    position: absolute;
    left: 58px;
    top: 186px;
    color: var(--brand-grey);
    font-weight: 600;
  }
  .wordmark__name { font-size: 44px; line-height: 1; display: block; margin-left: 58px; }
  .wordmark__tagline { font-size: 21px; font-weight: 600; letter-spacing: 0.5px; display: block; margin-top: 10px; }

  .holder {
    position: absolute;
    right: 54px;
    top: 58px;
    text-align: right;
  }
  .holder__name {
    font-family: "Noto Serif", serif;
    font-weight: 700;
    font-size: 50px;
    line-height: 1.1;
    color: var(--brand-blue);
  }
  .holder__title { font-size: 26px; line-height: 1.2; color: var(--ink); }

  .contacts {
    position: absolute;
    left: 60px;
    top: 302px;
    list-style: none;
  }
  .contacts__item {
    display: flex;
    align-items: flex-start;
    font-size: 24px;
    line-height: 40px;
  }
  .contacts__icon { width: 22px; height: 22px; margin-top: 9px; margin-right: 28px; flex: none; }
  .contacts__item--address { line-height: 38px; }

  /* Back */
  .services__heading {
    position: absolute;
    left: 147px;
    top: 40px;
    font-size: 58px;
    font-weight: 400;
    line-height: 1;
    color: var(--brand-blue);
  }
  .services__mark {
    position: absolute;
    left: 34px;
    top: 70px;
    width: 64px;
    height: 64px;
    border-radius: 50%;
    background: var(--brand-teal);
  }
  .services__rule {
    position: absolute;
    left: 96px;
    right: 0;
    top: 112px;
    height: 2px;
    background: var(--brand-teal);
  }
  .services__list {
    position: absolute;
    left: 221px;
    top: 146px;
    list-style: none;
  }
  .services__item {
    display: flex;
    align-items: center;
    font-size: 29px;
    line-height: 49.3px;
  }
  .services__bullet {
    width: 22px;
    height: 22px;
    border-radius: 50%;
    background: var(--brand-teal);
    margin-right: 22px;
    flex: none;
  }
</style>
</head>
<body>

<section class="card card--front" aria-label="Business card front">
  <div class="accent-disc"></div>

  <div class="wordmark">
    <span class="wordmark__name">BrightPath</span>
    <span class="wordmark__tagline">Chiropractic &amp; Holistic Center</span>
  </div>

  <div class="holder">
    <p class="holder__name">Daniel Reyes</p>
    <p class="holder__title">President</p>
  </div>

  <ul class="contacts">
    <li class="contacts__item">
      <svg class="contacts__icon" viewBox="0 0 22 22" aria-hidden="true">
        <rect width="22" height="22" fill="var(--brand-blue)"/>
        <path d="M7 4 L10 4 L10 8 L8.5 9 Q9.5 12 12.5 14 L13.5 12 L17 13 L17 17 Q10 18 6 11 Q5 7 7 4 Z" fill="var(--white)"/>
      </svg>
      <span>281-555-0193</span>
    </li>
    <li class="contacts__item">
      <svg class="contacts__icon" viewBox="0 0 22 22" aria-hidden="true">
        <rect width="22" height="22" fill="var(--brand-blue)"/>
        <circle cx="11" cy="11" r="7" fill="none" stroke="var(--white)" stroke-width="1.6"/>
        <ellipse cx="11" cy="11" rx="3" ry="7" fill="none" stroke="var(--white)" stroke-width="1.3"/>
        <line x1="4" y1="11" x2="18" y2="11" stroke="var(--white)" stroke-width="1.3"/>
      </svg>
      <span>www.brightpathhealth.com</span>
    </li>
    <li class="contacts__item">
      <svg class="contacts__icon" viewBox="0 0 22 22" aria-hidden="true">
        <rect width="22" height="22" fill="var(--brand-blue)"/>
        <rect x="4" y="6" width="14" height="10" fill="none" stroke="var(--white)" stroke-width="1.5"/>
        <path d="M4 6 L11 12 L18 6" fill="none" stroke="var(--white)" stroke-width="1.5"/>
      </svg>
      <span>hello@brightpathhealth.com</span>
    </li>
    <li class="contacts__item contacts__item--address">
      <svg class="contacts__icon" viewBox="0 0 22 22" aria-hidden="true">
        <rect width="22" height="22" fill="var(--brand-blue)"/>
        <path d="M11 4 Q16 4 16 9 Q16 12 11 18 Q6 12 6 9 Q6 4 11 4 Z" fill="var(--white)"/>
        <circle cx="11" cy="9" r="2" fill="var(--brand-blue)"/>
      </svg>
      <span>Marlene Okafor LMT, 4215 Elm Ridge Rd.<br>Suite 310, Missouri City, TX 77482</span>
    </li>
  </ul>
</section>

<section class="card card--back" aria-label="Business card back">
  <div class="accent-disc"></div>

  <div class="services__mark"></div>
  <h2 class="services__heading">services</h2>
  <div class="services__rule"></div>

  <ul class="services__list">
    <li class="services__item"><span class="services__bullet"></span>dietary &amp; fitness programs</li>
    <li class="services__item"><span class="services__bullet"></span>lymphatic &amp; therapeutic massage</li>
    <li class="services__item"><span class="services__bullet"></span>spinal exam</li>
    <li class="services__item"><span class="services__bullet"></span>health assessment</li>
    <li class="services__item"><span class="services__bullet"></span>far infrared sauna therapy</li>
    <li class="services__item"><span class="services__bullet"></span>restoration of health and vitality</li>
    <li class="services__item"><span class="services__bullet"></span>detox &amp; remineralize body wraps</li>
  </ul>
</section>

</body>
</html>
```